Corvane Holdings , new business card design

investment firm with corporate clients . need double sided business card , vertical and horizontal options ,logo must be clear. prefer pantone colors only and sharp design. website also www.corvane.ae

Khalid Bin Tarrafi
Managing Director
Tel. +971 4 387 2940
Mobile +971 50 518 2403
khalid@corvane.ae
Q-Span Plaza, officw 18-B07, Warqa Gardens, Dubai

Contact Information for Business Card

Khalid Bin Tarrafi
Managing Director

Font styles to use
Serif

Colors

Designer to choose colors to be used in the design.

```html
<!DOCTYPE html>
<html lang="en">
<head>
<meta charset="utf-8">
<title>Corvane Holdings — Business Card</title>
<link href="https://fonts.googleapis.com/css2?family=Questrial&family=Montserrat:wght@600&display=swap" rel="stylesheet">
<style>
  :root {
    --stage: #2e2e30;
    --card-white: #ffffff;
    --card-back: #f4f4f4;
    --steel-blue: #4a72a0;
    --charcoal: #3e3d40;
    --ink: #1f2328;
    --muted: #6b6d70;
    --text-light: #ffffff;
  }
  * { box-sizing: border-box; margin: 0; padding: 0; }
  html, body {
    width: 1200px; height: 900px; overflow: hidden;
    background: var(--stage);
    font-family: "Questrial", sans-serif;
  }
  .canvas { position: relative; width: 1200px; height: 900px; }
  .card {
    position: absolute; left: 250px; width: 700px; height: 400px;
    border-radius: 24px; overflow: hidden;
    box-shadow: 0 14px 30px rgba(0,0,0,0.45);
  }
  .card--front { top: 35px; background: var(--card-white); }
  .card--back { top: 465px; background: var(--card-back); }

  .card__band {
    position: absolute; left: 0; right: 0; top: 200px; bottom: 0;
    background: linear-gradient(100deg, var(--charcoal) 0%, var(--charcoal) 45%, var(--steel-blue) 75%, var(--steel-blue) 100%);
  }

  .wordmark {
    position: absolute; color: var(--ink);
    font-family: "Questrial", sans-serif; font-weight: 400;
    text-transform: uppercase; line-height: 1;
  }
  .wordmark__main { display: block; letter-spacing: 0.32em; }
  .wordmark__sub { display: block; letter-spacing: 0.62em; }
  .card--front .wordmark { right: 40px; top: 50px; text-align: right; }
  .card--front .wordmark__main { font-size: 40px; }
  .card--front .wordmark__sub { font-size: 15px; margin-top: 12px; }
  .card--back .wordmark { left: 0; right: 0; top: 128px; text-align: center; }
  .card--back .wordmark__main { font-size: 58px; padding-left: 0.32em; }
  .card--back .wordmark__sub { font-size: 20px; margin-top: 14px; padding-left: 0.62em; }

  .holder {
    position: absolute; left: 38px; bottom: 60px; color: var(--text-light);
  }
  .holder__name {
    font-family: "Montserrat", sans-serif; font-weight: 600;
    font-size: 19px; letter-spacing: 0.01em; text-transform: uppercase;
  }
  .holder__role { font-size: 18px; margin-top: 6px; }
  .holder__mobile { font-size: 18px; margin-top: 6px; display: flex; align-items: center; gap: 8px; }

  .contact {
    position: absolute; right: 32px; bottom: 48px;
    color: var(--text-light); text-align: right; font-size: 17px; line-height: 1.55;
  }
  .contact__line { display: flex; justify-content: flex-end; align-items: center; gap: 8px; }
  .icon { width: 14px; height: 14px; flex: none; }

  .website {
    position: absolute; left: 0; right: 0; bottom: 78px; text-align: center;
    color: var(--muted); font-size: 20px; letter-spacing: 0.55em; padding-left: 0.55em;
  }
</style>
</head>
<body>
<main class="canvas">

  <section class="card card--front" aria-label="Business card front">
    <div class="card__band" role="img" aria-label="Decorative sweep of charcoal and steel blue bands with a silver ribbon"></div>

    <div class="wordmark">
      <span class="wordmark__main">Corvane</span>
      <span class="wordmark__sub">Holdings</span>
    </div>

    <div class="holder">
      <p class="holder__name">Khalid Bin Tarrafi</p>
      <p class="holder__role">Managing Director</p>
      <p class="holder__mobile">
        <svg class="icon" viewBox="0 0 14 14" aria-hidden="true"><rect x="3.5" y="1" width="7" height="12" rx="1.5" fill="none" stroke="#fff" stroke-width="1.3"/><line x1="6" y1="11" x2="8" y2="11" stroke="#fff" stroke-width="1.2"/></svg>
        +971 50 518 2403
      </p>
    </div>

    <div class="contact">
      <p class="contact__line">+971 4 387 2940
        <svg class="icon" viewBox="0 0 14 14" aria-hidden="true"><path d="M3 1.5 L5.5 1.5 L6.3 4.5 L4.8 5.6 C5.6 7.4 6.8 8.6 8.5 9.3 L9.6 7.8 L12.5 8.6 L12.5 11.2 C12.5 12 11.8 12.6 11 12.5 C5.8 12 2 8.2 1.5 3 C1.4 2.2 2.1 1.5 3 1.5 Z" fill="#fff"/></svg>
      </p>
      <p class="contact__line">khalid@corvane.ae
        <svg class="icon" viewBox="0 0 14 14" aria-hidden="true"><rect x="1" y="3" width="12" height="8.5" rx="1" fill="#fff"/><path d="M1.5 3.5 L7 8 L12.5 3.5" fill="none" stroke="var(--steel-blue)" stroke-width="1.2"/></svg>
      </p>
      <p>Q-Span Plaza, officw 18-B07,</p>
      <p>Warqa Gardens, Dubai</p>
    </div>
  </section>

  <section class="card card--back" aria-label="Business card back">
    <div class="wordmark">
      <span class="wordmark__main">Corvane</span>
      <span class="wordmark__sub">Holdings</span>
    </div>
    <p class="website">www.corvane.ae</p>
  </section>

</main>
</body>
</html>
```